New Business Card Design Project

I'd like a business card design around the same modern style that I used on my website www.brovanhs.com
It's gonna be one of those round corners double-sided business cards with maybe a big logo on the front and all the info on the back of the card.

Contact Information for Business Card

Marco Delgado
425-317-6084
www.brovanhs.com

www.facebook.com/BrovanHomeServices
www.intsgram.com/BrovanHomeServices

Requirements
Must have
• it needs to look elegant and modern

```html
<!DOCTYPE html>
<html lang="en">
<head>
<meta charset="utf-8">
<title>Brovan Home Services — Business Card</title>
<link href="https://fonts.googleapis.com/css2?family=Open+Sans:wght@400;600;800&display=swap" rel="stylesheet">
<style>
  :root {
    --bg: #e8e9eb;
    --card-dark: #1b1c1e;
    --card-light: #ffffff;
    --brand-blue: #1e8fd8;
    --deep-blue: #1576bd;
    --charcoal: #2e2f33;
    --ink: #25272b;
    --muted: #4a4d52;
  }
  * { box-sizing: border-box; margin: 0; padding: 0; }
  html, body { width: 1200px; height: 715px; overflow: hidden; }
  body {
    background: var(--bg);
    font-family: "Open Sans", Arial, sans-serif;
    position: relative;
  }
  .card {
    position: absolute;
    top: 203px;
    width: 540px;
    height: 309px;
    border-radius: 14px;
    overflow: hidden;
    box-shadow: 0 8px 24px rgba(0,0,0,.18);
  }
  /* Front */
  .card-front {
    left: 40px;
    background: var(--card-dark);
    border-bottom: 4px solid var(--brand-blue);
    display: flex;
    flex-direction: column;
    align-items: center;
    justify-content: center;
  }
  .wordmark {
    color: var(--brand-blue);
    font-weight: 800;
    line-height: 1;
    text-align: center;
  }
  .card-front .wordmark-name { font-size: 74px; letter-spacing: -1px; }
  .card-front .wordmark-tag { font-size: 14px; letter-spacing: 2px; margin-top: 6px; }

  /* Back */
  .card-back {
    left: 620px;
    background: var(--card-light);
  }
  .back-waves { position: absolute; inset: 0; width: 540px; height: 309px; }
  .back-logo { position: absolute; left: 32px; top: 44px; }
  .card-back .wordmark-name { font-size: 50px; letter-spacing: -1px; text-align: left; }
  .card-back .wordmark-tag { font-size: 10px; letter-spacing: 1.5px; margin-top: 4px; text-align: left; }
  .divider {
    position: absolute;
    left: 32px; right: 30px; top: 192px;
    height: 1px;
    background: var(--brand-blue);
  }
  .holder {
    position: absolute;
    right: 30px; top: 156px;
    text-align: right;
  }
  .holder-name {
    color: var(--brand-blue);
    font-size: 24px;
    font-weight: 600;
    letter-spacing: 1px;
    text-transform: uppercase;
    line-height: 1;
  }
  .holder-role {
    color: var(--ink);
    font-size: 12px;
    margin-top: 12px;
  }
  .contact-list {
    position: absolute;
    left: 32px; top: 206px;
    list-style: none;
    color: var(--muted);
    font-size: 11.5px;
    line-height: 16px;
  }
  .contact-list li { display: flex; align-items: center; gap: 7px; }
  .contact-list svg { width: 9px; height: 9px; flex: none; fill: var(--muted); }
  .address {
    position: absolute;
    right: 30px; bottom: 30px;
    text-align: right;
    color: var(--ink);
    font-size: 12.5px;
    line-height: 19px;
  }
</style>
</head>
<body>

<section class="card card-front" aria-label="Card front">
  <div class="wordmark">
    <div class="wordmark-name">Brovan</div>
    <div class="wordmark-tag">HOME SERVICES</div>
  </div>
</section>

<section class="card card-back" aria-label="Card back">
  <svg class="back-waves" viewBox="0 0 540 309" aria-hidden="true">
    <path d="M60 0 H200 C150 7 100 9 60 0 Z" fill="var(--brand-blue)"/>
    <path d="M170 0 C280 5 300 112 392 144 C456 166 510 163 540 165" fill="none" stroke="var(--charcoal)" stroke-width="8"/>
    <path d="M200 0 C300 0 322 100 402 130 C462 150 510 148 540 150 L540 0 Z" fill="var(--brand-blue)"/>
  </svg>

  <div class="back-logo wordmark">
    <div class="wordmark-name">Brovan</div>
    <div class="wordmark-tag">HOME SERVICES</div>
  </div>

  <div class="holder">
    <div class="holder-name">Marco Delgado</div>
  </div>
  <div class="divider"></div>
  <div class="holder" style="top:200px"><div class="holder-role" style="margin-top:0">Director</div></div>

  <ul class="contact-list">
    <li><svg viewBox="0 0 10 10"><path d="M2 0.5 L4 2.8 L3 4 C3.8 5.6 4.6 6.4 6 7 L7.2 6 L9.5 8 L8 9.6 C4.5 9.2 0.8 5.5 0.4 2 Z"/></svg>425-317-6084</li>
    <li><svg viewBox="0 0 10 10"><path d="M0.5 2 H9.5 V8 H0.5 Z M1.5 3 L5 5.6 L8.5 3" fill="none" stroke="var(--muted)" stroke-width="1"/></svg>info@brovanhs.com</li>
    <li><svg viewBox="0 0 10 10"><circle cx="5" cy="5" r="4.2" fill="none" stroke="var(--muted)" stroke-width="1"/><path d="M1 5 H9 M5 0.8 C2.5 3 2.5 7 5 9.2 C7.5 7 7.5 3 5 0.8" fill="none" stroke="var(--muted)" stroke-width=".8"/></svg>www.brovanhs.com</li>
    <li><svg viewBox="0 0 10 10"><rect x="1.5" y="1.5" width="7" height="7"/></svg>/BrovanHomeServices</li>
    <li><svg viewBox="0 0 10 10"><rect x="1.5" y="1.5" width="7" height="7"/></svg>/BrovanHomeServices</li>
  </ul>

  <address class="address" style="font-style:normal">
    2417 Carden Hollow Road<br>
    Tulsa, OK 74105
  </address>
</section>

</body>
</html>
```